Parcelwise HQ letterhead and envelope

Design a formal (8.5x11) letterhead and envelope for sales outreach and legal matters. Using design input from https://www.parcelwisehq.example/ and the attached documents.

Industry/Entity Type

Software Service

Requirements
Must have
• These 4 hex colors are our official colors:
• #355c98 [blue]
• #1eb1a2 [teal]
• #fdba12 [gold]
• #f1653b [orange]
• So no other colors besides these should be used.

```html
<!DOCTYPE html>
<html lang="en">
<head>
<meta charset="utf-8">
<title>Parcelwise HQ Letterhead</title>
<link href="https://fonts.googleapis.com/css2?family=Open+Sans:wght@300;400;700&display=swap" rel="stylesheet">
<style>
  :root {
    --brand-blue: #355c98;
    --brand-teal: #1eb1a2;
    --backdrop: #e4e5e6;
    --paper: #fafafa;
    --ink: #2b2b2b;
    --ink-soft: #4a4a4a;
  }
  * { box-sizing: border-box; margin: 0; padding: 0; }
  html, body { width: 1200px; height: 945px; overflow: hidden; }
  body {
    background: var(--backdrop);
    font-family: "Open Sans", Arial, sans-serif;
    position: relative;
  }
  .letterhead {
    position: absolute;
    left: 252px; top: 22px;
    width: 696px; height: 900px;
    background: var(--paper);
    box-shadow: 0 6px 18px rgba(0,0,0,0.18);
    overflow: hidden;
  }
  .brand {
    position: absolute;
    top: 48px; left: 0; right: 0;
    display: flex; justify-content: center; align-items: center; gap: 10px;
    color: var(--brand-blue);
  }
  .brand-dot {
    width: 26px; height: 26px;
    border: 3px solid var(--brand-blue);
    border-radius: 50%;
  }
  .brand-name {
    font-weight: 300;
    font-size: 26px;
    letter-spacing: 0.5px;
  }
  .letter-body {
    position: absolute;
    top: 210px; left: 72px; right: 72px;
    color: var(--ink-soft);
    font-size: 12.5px;
    line-height: 1.38;
  }
  .salutation {
    font-weight: 700;
    font-size: 14px;
    color: var(--ink);
    margin-bottom: 14px;
  }
  .letter-body p { margin-bottom: 16px; }
  .signature {
    margin-top: 34px;
    width: 130px; height: 46px;
    background: linear-gradient(90deg, #d8d8d8, #ececec);
    border-radius: 4px;
  }
  .footer-band {
    position: absolute;
    left: 0; bottom: 0;
    width: 696px; height: 190px;
  }
  .contact {
    position: absolute;
    right: 34px; bottom: 26px;
    color: #fff;
    font-size: 11px;
    text-align: right;
    line-height: 1.6;
  }
  .contact-line { display: flex; gap: 12px; justify-content: flex-end; align-items: center; }
  .contact-item { display: inline-flex; align-items: center; gap: 4px; }
  .contact-item svg { width: 10px; height: 10px; }
</style>
</head>
<body>
  <main class="letterhead">
    <header class="brand">
      <span class="brand-dot"></span>
      <span class="brand-name">Parcelwise HQ</span>
    </header>

    <section class="letter-body">
      <p class="salutation">Dear Mr. John,</p>
      <p>Lorem Ipsum is simply dummy text of the printing and typesetting industry. Lorem Ipsum has been the industry's standard dummy text ever since the 1500s, when an unknown printer took a galley of type and scrambled it to make a type specimen book. It has survived not only five centuries, but also the leap into electronic typesetting, remaining essentially unchanged.</p>
      <p>The standard chunk of Lorem Ipsum used since the 1500s is reproduced below for those interested. Sections 1.10.32 and 1.10.33 from "de Finibus Bonorum et Malorum" by Cicero are also reproduced in their exact original form, accompanied by English versions from the 1914 translation by H. Rackham</p>
      <p>Lorem Ipsum is simply dummy text of the printing and typesetting industry. Lorem Ipsum has been the industry's standard dummy text ever since the 1500s, when an unknown printer took a galley of type and scrambled it to make a type specimen book. It has survived not only five centuries, but also the leap into electronic typesetting, remaining essentially unchanged. It was popularised in the</p>
      <p>The standard chunk of Lorem Ipsum used since the 1500s is reproduced below for those interested. Sections 1.10.32 and 1.10.33 from "de Finibus Bonorum et Malorum" by Cicero are also reproduced in their exact original form, accompanied by English versions from the 1914 translation by H. Rackham</p>
      <p>The standard chunk of Lorem Ipsum used since the 1500s is reproduced below for those interested. Sections 1.10.32 and 1.10.33 from "de Finibus Bonorum et Malorum" by Cicero are also reproduced in their exact original form.</p>
      <div class="signature" role="img" aria-label="Handwritten signature of the sender"></div>
    </section>

    <svg class="footer-band" viewBox="0 0 696 190" preserveAspectRatio="none" aria-hidden="true">
      <path d="M0,190 Q300,70 696,22 L696,190 Z" fill="var(--brand-blue)"/>
      <path d="M0,184 Q290,58 696,10" fill="none" stroke="var(--brand-teal)" stroke-width="3"/>
    </svg>

    <footer class="contact">
      <div>82 Harbor Lane Springfield, ST 00000</div>
      <div class="contact-line">
        <span class="contact-item">
          <svg viewBox="0 0 10 10"><path d="M2 1 L4 3 L3 4 Q4 6 6 7 L7 6 L9 8 L8 9 Q3 9 1 2 Z" fill="#fff"/></svg>
          (555) 014-2287
        </span>
        <span class="contact-item">
          <svg viewBox="0 0 10 10"><rect x="1" y="2" width="8" height="6" fill="none" stroke="#fff"/><path d="M1 2 L5 5.5 L9 2" fill="none" stroke="#fff"/></svg>
          jsmith@parcelwisehq.example
        </span>
        <span class="contact-item">
          <svg viewBox="0 0 10 10"><circle cx="5" cy="5" r="4" fill="none" stroke="#fff"/><path d="M1 5 H9 M5 1 Q2.5 5 5 9 Q7.5 5 5 1" fill="none" stroke="#fff" stroke-width="0.8"/></svg>
          www.parcelwisehq.example
        </span>
      </div>
    </footer>
  </main>
</body>
</html>
```